Business Card for a Jewellery Brand

Business card for an upscale jewellery brand. Attached is the brand logo and icon and color board. I am looking for two card versions: one for the founder and one is generic. The card should be elegant and convey upscale and premium feel. I am open to both square and rectangle card shapes.

Industry/Entity Type

Jewelry

Contact Information for Business Card

Two cards: (1) Sunela Parvaniya (Founder) (2) General
(1) Sunela Parvaniya card should have Name: Sunela Parvaniya, Title: Founder Email id: sunela@quiremo.com.au. Phone no: +61452913307
(2) Generic card should have Email id: info@quiremo.com.au. Phone no: +61436207518

Requirements
Must have
• Workmark
• ICON
• Phone no
• Email ID
• ABN: 58219740312 (Note: ABN is Business number in Australia)
• Website: www.quiremo.com.au
• Instagram: quiremo_jewellery
• Facebook: @quiremojewellery
Nice to have
• Tagline

```html
<!DOCTYPE html>
<html lang="en">
<head>
<meta charset="UTF-8">
<title>Quiremo Business Cards</title>
<link rel="stylesheet" href="https://fonts.googleapis.com/css2?family=Jost:wght@300;400;500&display=swap">
<style>
  :root {
    --backdrop: #1c1c1d;
    --card: #131314;
    --rose: #e8958f;
    --ink-light: #f2eeee;
  }
  * { margin: 0; padding: 0; box-sizing: border-box; }
  html, body {
    width: 1200px; height: 929px; overflow: hidden;
    background: radial-gradient(ellipse at 50% 40%, #2a2a2b 0%, var(--backdrop) 70%);
    font-family: "Jost", sans-serif;
  }
  .card {
    position: absolute;
    width: 540px; height: 308px;
    background: var(--card);
    box-shadow: 0 18px 40px rgba(0,0,0,.55);
    overflow: hidden;
  }
  .card-band {
    position: absolute; left: 0; right: 0; bottom: 0;
    height: 12px; background: var(--rose);
  }
  /* front */
  .card-front { left: 90px; top: 110px; }
  .front-brand {
    position: absolute; left: 0; right: 0; top: 112px;
    text-align: center;
  }
  .front-brand .brand-dot {
    display: inline-block; width: 14px; height: 14px;
    background: var(--rose); border-radius: 50%;
    margin-bottom: 16px;
  }
  .front-brand .brand-name {
    display: block;
    color: var(--rose); font-weight: 400;
    font-size: 40px; letter-spacing: 14px;
    padding-left: 14px;
  }
  /* back */
  .card-back { left: 570px; top: 480px; }
  .back-brand {
    position: absolute; left: 34px; top: 88px;
    color: var(--rose); font-weight: 400;
    font-size: 46px; letter-spacing: 14px;
  }
  .abn {
    position: absolute; right: 34px; top: 26px;
    font-size: 13px; color: var(--ink-light); letter-spacing: 1px;
  }
  .abn .label, .social .label { color: var(--rose); }
  .person {
    position: absolute; right: 34px; top: 100px; text-align: right;
  }
  .person-name {
    color: var(--rose); font-size: 17px; letter-spacing: 1.5px;
    text-transform: uppercase; font-weight: 400;
  }
  .person-title {
    color: var(--ink-light); font-size: 13px; letter-spacing: 1px;
  }
  .divider {
    position: absolute; left: 34px; right: 180px; top: 182px;
    height: 1px; background: var(--rose);
  }
  .contact {
    position: absolute; left: 34px; top: 196px;
    list-style: none;
  }
  .contact li {
    display: flex; align-items: center; gap: 10px;
    color: var(--ink-light); font-size: 13px; letter-spacing: 1px;
    font-weight: 300; line-height: 24px;
  }
  .contact svg { width: 13px; height: 13px; flex: none; }
  .social {
    position: absolute; right: 34px; top: 212px;
    color: var(--ink-light); font-size: 13px; letter-spacing: .8px;
    font-weight: 300; line-height: 22px;
  }
</style>
</head>
<body>
  <section class="card card-front">
    <div class="front-brand">
      <span class="brand-dot"></span>
      <span class="brand-name">QUIREMO</span>
    </div>
    <div class="card-band"></div>
  </section>

  <section class="card card-back">
    <div class="abn"><span class="label">ABN:</span> 58219740312</div>
    <div class="back-brand">QUIREMO</div>
    <div class="person">
      <div class="person-name">Sunela Parvaniya</div>
      <div class="person-title">FOUNDER</div>
    </div>
    <div class="divider"></div>
    <ul class="contact">
      <li>
        <svg viewBox="0 0 14 14" fill="none" stroke="#e8958f" stroke-width="1.4"><rect x="3.5" y="1" width="7" height="12" rx="1.2"/><line x1="6" y1="11" x2="8" y2="11"/></svg>
        +61452913307
      </li>
      <li>
        <svg viewBox="0 0 14 14" fill="none" stroke="#e8958f" stroke-width="1.3"><circle cx="7" cy="7" r="5.8"/><ellipse cx="7" cy="7" rx="2.5" ry="5.8"/><line x1="1.2" y1="7" x2="12.8" y2="7"/></svg>
        www.quiremo.com.au
      </li>
      <li>
        <svg viewBox="0 0 14 14" fill="none" stroke="#e8958f" stroke-width="1.4"><rect x="1" y="3" width="12" height="8.5"/><polyline points="1,3 7,8 13,3"/></svg>
        sunela@quiremo.com.au
      </li>
    </ul>
    <div class="social">
      <div><span class="label">Ins:</span> quiremo_jewellery</div>
      <div><span class="label">Fb:</span> @quiremojewellery</div>
    </div>
    <div class="card-band"></div>
  </section>
</body>
</html>
```